Looking for business card/letterhead/email signature

Take existing logo and create full design suite of collateral

Contact Information for Business Card

Use mock details that can be edited by us

Font styles to use
Sans Serif

```html
<!DOCTYPE html>
<html lang="en">
<head>
<meta charset="utf-8">
<title>Norvale Digital — Stationery Suite</title>
<link rel="stylesheet" href="https://fonts.googleapis.com/css2?family=Montserrat:wght@400;500;700&family=Roboto:wght@400;500;700&display=swap">
<style>
:root{
  --brand-blue:#0b4f93;
  --ink:#3a3a3a;
  --muted:#6b6b6b;
  --paper:#ffffff;
  --paper-soft:#f6f6f6;
  --scene:#e4e4e4;
  --s1:#1b4f8c;
  --s2:#3aa6dd;
  --s3:#c4d534;
  --s4:#f29a38;
  --s5:#e8427c;
  --s6:#e02b4f;
  --sans:"Montserrat",sans-serif;
  --contact:"Roboto",sans-serif;
}
*{margin:0;padding:0;box-sizing:border-box}
html,body{width:1200px;height:796px;overflow:hidden;background:var(--scene);font-family:var(--sans);color:var(--ink)}
.canvas{position:relative;width:1200px;height:796px}
.sheet{position:absolute;background:var(--paper);box-shadow:0 1px 4px rgba(0,0,0,.18)}

/* wordmark */
.wordmark{display:inline-flex;align-items:center;gap:.25em;font-family:var(--sans);font-weight:700;color:var(--brand-blue);white-space:nowrap;letter-spacing:-.01em}
.wordmark .dot{width:.45em;height:.45em;border-radius:50%;background:currentColor}
.wordmark.on-blue{color:#fff}

/* colour stripe */
.stripe{position:absolute;display:flex;gap:3px;height:1.2px}
.stripe i{flex:1;display:block}
.stripe i:nth-child(1){background:var(--s1)}
.stripe i:nth-child(2){background:var(--s2)}
.stripe i:nth-child(3){background:var(--s3)}
.stripe i:nth-child(4){background:var(--s4)}
.stripe i:nth-child(5){background:var(--s5)}
.stripe i:nth-child(6){background:var(--s6)}

.center-x{position:absolute;left:0;right:0;display:flex;justify-content:center}

/* letterhead */
.letterhead{left:342px;top:78px;width:336px;height:472px}
.letterhead .greeting{position:absolute;left:30px;top:133px;font-size:8px;color:var(--muted)}
.letterhead .body{position:absolute;left:30px;top:158px;width:278px;font-size:4.6px;line-height:7.2px;color:var(--muted);text-align:justify}
.letterhead .body p{margin-bottom:7px}
.letterhead .closing{position:absolute;left:30px;top:308px;font-size:4.8px;color:var(--muted)}
.letterhead .signature{position:absolute;left:26px;top:326px;width:64px;height:22px;background:linear-gradient(90deg,rgba(60,100,170,.18),rgba(60,100,170,.05));border-radius:3px}
.letterhead .stripe{left:30px;right:28px;top:414px}
.contact-list{position:absolute;list-style:none;font-family:var(--contact);color:var(--muted)}
.contact-list li{display:flex;align-items:center;gap:3px}
.contact-list svg{fill:var(--brand-blue);flex:none}
.letterhead .contact-list{left:30px;top:422px;font-size:4.6px;line-height:6px}
.letterhead .address{position:absolute;right:28px;top:422px;font-size:4.6px;line-height:6px;text-align:right;color:var(--muted);font-family:var(--contact)}

/* folder */
.folder{left:706px;top:50px;width:395px;height:501px;background:var(--brand-blue)}
.folder .spine{position:absolute;top:0;bottom:0;width:1px;background:rgba(255,255,255,.22)}
.folder .logo{top:275px;font-size:38px}

/* business cards */
.card-blue{left:158px;top:357px;width:153px;height:88px;background:var(--brand-blue)}
.card-blue .logo{top:30px;font-size:15px}
.card-blue .web{position:absolute;left:0;right:0;top:74px;text-align:center;font-size:3.4px;letter-spacing:.12em;color:rgba(255,255,255,.8)}

.card-small{left:158px;top:461px;width:154px;height:88px;background:var(--paper-soft)}
.card-small .logo{top:19px;font-size:13px}
.card-small .stripe{left:11px;right:12px;top:53px;height:.8px;gap:2px}
.card-small .person{position:absolute;left:11px;top:57px;font-family:var(--contact);font-size:4px;line-height:4.6px;color:var(--muted)}
.card-small .person strong{color:var(--brand-blue);font-size:4.8px}
.card-small .contact-list{right:12px;top:57px;font-size:3.4px;line-height:4.6px;text-align:right}
.card-small .contact-list li{justify-content:flex-end}

.card-large{left:42px;top:606px;width:306px;height:147px;background:var(--paper-soft)}
.card-large .logo{top:38px;font-size:24px}
.card-large .stripe{left:20px;right:20px;top:90px;height:1.4px}
.card-large .person{position:absolute;left:20px;top:98px;font-family:var(--contact);font-size:7px;line-height:8.6px;color:var(--muted)}
.card-large .person strong{display:block;color:var(--brand-blue);font-size:9px;font-weight:500}
.card-large .person .role{color:#333}
.card-large .contact-list{right:20px;top:98px;font-size:7px;line-height:8.6px}
.card-large .contact-list li{justify-content:flex-end}

/* envelopes */
.envelope-front{left:369px;top:580px;width:386px;height:176px}
.envelope-front .logo{position:absolute;left:24px;top:44px;font-size:20px}
.envelope-front .stripe{left:22px;right:24px;top:144px}
.envelope-front .address{position:absolute;left:22px;top:150px;font-family:var(--contact);font-size:4.4px;line-height:5.6px;color:var(--muted)}

.envelope-back{left:774px;top:578px;width:386px;height:175px;background:#f3f3f3}
.envelope-back .flap{position:absolute;left:0;top:0;width:386px;height:56px}
.envelope-back .logo{top:22px;font-size:13px}
</style>
</head>
<body>
<svg width="0" height="0" style="position:absolute" aria-hidden="true">
  <symbol id="icon-phone" viewBox="0 0 10 10"><path d="M2 1l2 2-1 1.2c.6 1.2 1.6 2.2 2.8 2.8L7 6l2 2-1.2 1.2C4.6 9 1 5.4.8 2.2z"/></symbol>
  <symbol id="icon-mobile" viewBox="0 0 10 10"><path d="M3 .5h4a.8.8 0 0 1 .8.8v7.4a.8.8 0 0 1-.8.8H3a.8.8 0 0 1-.8-.8V1.3A.8.8 0 0 1 3 .5zm.4 1.2v5.8h3.2V1.7z"/></symbol>
  <symbol id="icon-fax" viewBox="0 0 10 10"><path d="M2.5 1h5v2.5h-5zM1 4h8v4H7.5v1h-5V8H1zm2.5 2.5v1.8h3V6.5z"/></symbol>
  <symbol id="icon-mail" viewBox="0 0 10 10"><path d="M.5 2h9v6h-9zm.8.8v.3L5 5.5l3.7-2.4v-.3z"/></symbol>
</svg>

<main class="canvas">

  <!-- Business card, front -->
  <section class="sheet card-blue">
    <div class="center-x logo"><span class="wordmark on-blue">Norvale Digital<span class="dot"></span></span></div>
    <p class="web">www.norvale.co</p>
  </section>

  <!-- Business card, back (small) -->
  <section class="sheet card-small">
    <div class="center-x logo"><span class="wordmark">Norvale Digital<span class="dot"></span></span></div>
    <div class="stripe"><i></i><i></i><i></i><i></i><i></i><i></i></div>
    <p class="person"><strong>DANIEL REYES</strong><br>CEO/FOUNDER<br>2140 Alder Street<br>Fairbanks, Alaska 99701</p>
    <ul class="contact-list">
      <li>555 201 3847 <svg width="4" height="4"><use href="#icon-phone"/></svg></li>
      <li>555 312 7740 <svg width="4" height="4"><use href="#icon-mobile"/></svg></li>
      <li>555 468 0925 <svg width="4" height="4"><use href="#icon-fax"/></svg></li>
      <li>hello@norvale.co <svg width="4" height="4"><use href="#icon-mail"/></svg></li>
    </ul>
  </section>

  <!-- Letterhead -->
  <section class="sheet letterhead">
    <div class="center-x" style="top:50px;font-size:17px"><span class="wordmark">Norvale Digital<span class="dot"></span></span></div>
    <p class="greeting">Dear Mr. Reyes,</p>
    <div class="body">
      <p>Thank you for meeting with our team last week. We enjoyed learning about your plans for the coming season and the goals you shared for the new campaign. This letter outlines the next steps we discussed together.</p>
      <p>Our designers will prepare three initial concepts for review within two weeks. Each concept will include a colour palette, type choices and sample layouts for print and screen so you can compare them side by side.</p>
      <p>Once a direction is chosen, we will refine the details and build the full stationery set, including cards, letterhead, envelopes and a presentation folder. Final files will be delivered in formats ready for your printer.</p>
      <p>Please let us know if you have any questions in the meantime. We look forward to working with you on this project.</p>
    </div>
    <p class="closing">Sincerely,</p>
    <div class="signature" role="img" aria-label="Handwritten signature"></div>
    <div class="stripe"><i></i><i></i><i></i><i></i><i></i><i></i></div>
    <ul class="contact-list">
      <li><svg width="4" height="4"><use href="#icon-phone"/></svg>555 201 3847</li>
      <li><svg width="4" height="4"><use href="#icon-mobile"/></svg>555 312 7740</li>
      <li><svg width="4" height="4"><use href="#icon-fax"/></svg>555 468 0925</li>
      <li><svg width="4" height="4"><use href="#icon-mail"/></svg>hello@norvale.co</li>
    </ul>
    <p class="address">2140 Alder Street<br>Fairbanks<br>Alaska 99701<br>www.norvale.co</p>
  </section>

  <!-- Presentation folder -->
  <section class="sheet folder">
    <span class="spine" style="left:11px"></span>
    <span class="spine" style="left:14px"></span>
    <span class="spine" style="left:18px"></span>
    <div class="center-x logo"><span class="wordmark on-blue">Norvale Digital<span class="dot"></span></span></div>
  </section>

  <!-- Business card, large -->
  <section class="sheet card-large">
    <div class="center-x logo"><span class="wordmark">Norvale Digital<span class="dot"></span></span></div>
    <div class="stripe"><i></i><i></i><i></i><i></i><i></i><i></i></div>
    <p class="person"><strong>DANIEL REYES</strong><span class="role">CEO/FOUNDER</span><br>2140 Alder Street<br>Fairbanks, Alaska 99701</p>
    <ul class="contact-list">
      <li>555 201 3847 <svg width="7" height="7"><use href="#icon-phone"/></svg></li>
      <li>555 312 7740 <svg width="7" height="7"><use href="#icon-mobile"/></svg></li>
      <li>555 468 0925 <svg width="7" height="7"><use href="#icon-fax"/></svg></li>
      <li>hello@norvale.co <svg width="7" height="7"><use href="#icon-mail"/></svg></li>
    </ul>
  </section>

  <!-- Envelope, front -->
  <section class="sheet envelope-front">
    <span class="logo wordmark">Norvale Digital<span class="dot"></span></span>
    <div class="stripe"><i></i><i></i><i></i><i></i><i></i><i></i></div>
    <p class="address">2140 Alder Street<br>Fairbanks, Alaska 99701</p>
  </section>

  <!-- Envelope, back -->
  <section class="sheet envelope-back">
    <svg class="flap" viewBox="0 0 386 56" preserveAspectRatio="none" aria-hidden="true">
      <path d="M0 0H386V4C380 8 376 20 372 36C369 48 362 54 348 54H38C24 54 17 48 14 36C10 20 6 8 0 4Z" fill="var(--brand-blue)"/>
    </svg>
    <div class="center-x logo"><span class="wordmark on-blue">Norvale Digital<span class="dot"></span></span></div>
  </section>

</main>
</body>
</html>
```